Heron Loan Partners Business Card

We need a business card design for our mortgage servicing company. In addition to servicing the loans of homeowners, we help homeowners with purchasing their homes and any mortgage refinancing. We would like to see designs that use the colors in the logo attached below (gold-ish yellow and navy blue), and any other design you deem fit! The design should communicate a simpler life with smart mortgages provided by Heron.

```html
<!DOCTYPE html>
<html lang="en">
<head>
<meta charset="utf-8">
<title>Heron Loan Partners – Business Card</title>
<link rel="stylesheet" href="https://fonts.googleapis.com/css2?family=Lato:wght@400;700;900&display=swap">
<style>
  :root {
    --backdrop: #2b2c30;
    --card-navy: #26225a;
    --card-edge: #1d1a4a;
    --gold: #f2b52b;
    --ink-light: #e9e8f2;
  }
  * { margin: 0; padding: 0; box-sizing: border-box; }
  html, body {
    width: 1200px; height: 952px; overflow: hidden;
    background: var(--backdrop);
    font-family: "Lato", sans-serif;
  }
  .sheet {
    width: 1200px; height: 952px;
    display: flex; flex-direction: column;
    align-items: center; justify-content: center; gap: 48px;
  }
  .card {
    position: relative;
    width: 700px; height: 400px;
    background: var(--card-navy);
    border-radius: 26px;
    box-shadow: 0 6px 0 var(--card-edge), 0 18px 40px rgba(0,0,0,.45);
    overflow: hidden;
  }
  .wordmark {
    display: flex; align-items: center; gap: 12px;
    color: var(--gold);
    font-weight: 900;
    white-space: nowrap;
  }
  .wordmark__dot {
    width: 14px; height: 14px; border-radius: 50%;
    background: var(--gold);
  }
  .card--front .wordmark {
    position: absolute; left: 50%; top: 50%;
    transform: translate(-50%, -50%);
    font-size: 46px;
  }
  .card--front .wordmark__dot { width: 20px; height: 20px; }
  .card--back .wordmark {
    position: absolute; left: 54px; top: 70px;
    font-size: 30px;
  }
  .contact {
    position: absolute; left: 360px; top: 150px;
    color: var(--ink-light);
  }
  .contact__name {
    font-size: 24px; font-weight: 400; letter-spacing: .5px;
    color: var(--gold); text-transform: uppercase;
  }
  .contact__name strong { font-weight: 900; }
  .contact__role { font-size: 17px; margin-top: 4px; }
  .contact__rule {
    width: 50px; height: 2px; background: var(--gold);
    margin: 12px 0 16px;
  }
  .contact__list { list-style: none; }
  .contact__item {
    display: flex; align-items: flex-start; gap: 12px;
    font-size: 15px; line-height: 1.35; margin-bottom: 9px;
  }
  .contact__icon {
    flex: none; width: 20px; height: 20px; border-radius: 4px;
    background: var(--gold);
    display: flex; align-items: center; justify-content: center;
  }
  .contact__item--address .contact__icon { background: var(--ink-light); }
</style>
</head>
<body>
<main class="sheet">
  <section class="card card--front" aria-label="Card front">
    <div class="wordmark"><span class="wordmark__dot"></span>Heron Loan Partners</div>
  </section>

  <section class="card card--back" aria-label="Card back">
    <div class="wordmark"><span class="wordmark__dot"></span>Heron Loan Partners</div>
    <div class="contact">
      <p class="contact__name">Daniel R. <strong>Whitford</strong></p>
      <p class="contact__role">Managing Director</p>
      <div class="contact__rule"></div>
      <ul class="contact__list">
        <li class="contact__item contact__item--address">
          <span class="contact__icon">
            <svg width="12" height="14" viewBox="0 0 12 14"><path d="M6 0a5 5 0 0 0-5 5c0 3.6 5 9 5 9s5-5.4 5-9a5 5 0 0 0-5-5z" fill="#26225a"/><circle cx="6" cy="5" r="1.8" fill="#e9e8f2"/></svg>
          </span>
          <span>2170 Harbor View Avenue<br>Annapolis, MD 21401</span>
        </li>
        <li class="contact__item">
          <span class="contact__icon">
            <svg width="12" height="12" viewBox="0 0 12 12"><path d="M2.5 0.8l2 2.4-1.2 1.4a7 7 0 0 0 4.1 4.1l1.4-1.2 2.4 2-1 1.7C5.5 11.5 0.5 6.5.8 1.8z" fill="#26225a"/></svg>
          </span>
          <span>+00 987 654 32</span>
        </li>
        <li class="contact__item">
          <span class="contact__icon">
            <svg width="12" height="10" viewBox="0 0 12 10"><rect x=".5" y=".5" width="11" height="9" rx="1" fill="none" stroke="#26225a" stroke-width="1.3"/><path d="M1 1l5 4 5-4" fill="none" stroke="#26225a" stroke-width="1.3"/></svg>
          </span>
          <span>hello@heronloan.com</span>
        </li>
        <li class="contact__item">
          <span class="contact__icon">
            <svg width="12" height="12" viewBox="0 0 12 12"><path d="M2 10L10 2M4 2h6v6" fill="none" stroke="#26225a" stroke-width="1.6"/></svg>
          </span>
          <span>www.heronloan.com</span>
        </li>
      </ul>
    </div>
  </section>
</main>
</body>
</html>
```